Web Developer Needs a Business Card Design

I need a personal business card design that represents me as a web developer for potential employers. I would like the background to be a dark color on the front for contrast with my logo and name. The back will have all my information along with a smaller version of the logo. I want something with a modern look and feel, not too conservative. This will be used for potential employers and freelance work.

Industry/Entity Type

Business

Contact Information for Business Card

Front should have my logo and name. The back should have all my personal information which would include: name: Tom Varulek, phone: 570-614-3098, email: tomvarulek@quillbox.net, website url: www.tomvarulek.net, logo, web developer.

Font styles to use
Sans Serif

Requirements
Must have
• Must include my logo. The color palette base color will be the logo color.

```html
<!DOCTYPE html>
<html lang="en">
<head>
<meta charset="utf-8">
<title>Tom Varulek – Business Card</title>
<link rel="stylesheet" href="https://fonts.googleapis.com/css2?family=Open+Sans:wght@400;600;700&display=swap">
<style>
  :root {
    --teal: #6fd0bb;
    --teal-deep: #4fbfa7;
    --ink: #111111;
    --paper: #ffffff;
    --stage: #e9e9e9;
    --muted: #2b2b2b;
  }
  * { box-sizing: border-box; margin: 0; padding: 0; }
  html, body { width: 1200px; height: 913px; overflow: hidden; }
  body {
    background: var(--stage);
    font-family: "Open Sans", Arial, sans-serif;
    position: relative;
  }
  .card {
    position: absolute;
    width: 520px;
    height: 298px;
    border-radius: 16px;
    overflow: hidden;
    box-shadow: 0 8px 24px rgba(0,0,0,0.18);
  }
  .card--back { left: 50px; top: 308px; background: var(--paper); }
  .card--front { left: 630px; top: 308px; background: var(--ink); }

  .back-art { position: absolute; inset: 0; }

  .mark {
    display: flex;
    align-items: center;
    gap: 10px;
    color: var(--teal);
    font-weight: 600;
  }
  .mark__ring {
    border: 6px solid var(--teal);
    border-radius: 50%;
    flex: none;
  }
  .card--back .mark {
    position: absolute;
    right: 26px;
    top: 58px;
    font-size: 20px;
    background: var(--paper);
    padding: 4px 8px;
  }
  .card--back .mark__ring { width: 52px; height: 52px; }

  .identity { position: absolute; left: 34px; top: 90px; }
  .identity__name {
    font-size: 21px;
    font-weight: 700;
    letter-spacing: 0.5px;
    color: var(--ink);
    text-transform: uppercase;
    line-height: 1.1;
  }
  .identity__role {
    font-size: 12.5px;
    font-weight: 600;
    letter-spacing: 0.6px;
    color: var(--teal);
    text-transform: uppercase;
    line-height: 1.3;
  }

  .contacts {
    position: absolute;
    left: 40px;
    top: 170px;
    list-style: none;
    font-size: 13px;
    color: var(--muted);
    line-height: 19px;
  }
  .contacts li { display: flex; align-items: center; gap: 8px; }
  .contacts svg { width: 11px; height: 11px; fill: var(--teal-deep); flex: none; }

  .front-block {
    position: absolute;
    inset: 0;
    display: flex;
    flex-direction: column;
    align-items: center;
    justify-content: center;
    color: var(--paper);
  }
  .card--front .mark { font-size: 22px; margin-bottom: 22px; }
  .card--front .mark__ring { width: 64px; height: 64px; border-width: 7px; }
  .front-block__name {
    font-size: 30px;
    font-weight: 400;
    letter-spacing: 2px;
    text-transform: uppercase;
    line-height: 1.1;
  }
  .front-block__role { font-size: 15px; margin-top: 8px; letter-spacing: 0.4px; }
</style>
</head>
<body>

  <section class="card card--back" aria-label="Card back with contact details">
    <svg class="back-art" viewBox="0 0 520 298" width="520" height="298" aria-hidden="true">
      <line x1="0" y1="162" x2="520" y2="88" stroke="#111" stroke-width="1.4"/>
      <path d="M0 254 C170 246 360 214 520 150 L520 166 C360 230 170 262 0 270 Z" fill="var(--teal)"/>
      <path d="M0 270 C170 262 360 230 520 166 L520 298 L0 298 Z" fill="var(--ink)"/>
    </svg>

    <div class="mark"><span class="mark__ring"></span>Varulek</div>

    <div class="identity">
      <h1 class="identity__name">Tom Varulek</h1>
      <p class="identity__role">Web Developer</p>
    </div>

    <ul class="contacts">
      <li><svg viewBox="0 0 24 24"><path d="M6.6 10.8a15.1 15.1 0 0 0 6.6 6.6l2.2-2.2c.3-.3.7-.4 1-.2 1.1.4 2.3.6 3.6.6.6 0 1 .4 1 1V20c0 .6-.4 1-1 1C10.6 21 3 13.4 3 4c0-.6.4-1 1-1h3.5c.6 0 1 .4 1 1 0 1.3.2 2.5.6 3.6.1.3 0 .7-.2 1z"/></svg>570-614-3098</li>
      <li><svg viewBox="0 0 24 24"><path d="M2 5h20v14H2zm2 2v.5l8 5 8-5V7zm0 2.8V17h16V9.8l-8 5z"/></svg>tomvarulek@quillbox.net</li>
      <li><svg viewBox="0 0 24 24"><path d="M12 2a10 10 0 1 0 0 20 10 10 0 0 0 0-20zm6.9 6h-3a15 15 0 0 0-1.3-3.9A8 8 0 0 1 18.9 8zM12 4c.8 1.2 1.5 2.5 1.9 4h-3.8c.4-1.5 1.1-2.8 1.9-4zM4.3 14a8 8 0 0 1 0-4h3.4a16 16 0 0 0 0 4zm.8 2h3a15 15 0 0 0 1.3 3.9A8 8 0 0 1 5.1 16zm3-8h-3a8 8 0 0 1 4.3-3.9C8.8 5.3 8.4 6.6 8.1 8zM12 20c-.8-1.2-1.5-2.5-1.9-4h3.8c-.4 1.5-1.1 2.8-1.9 4zm2.3-6H9.7a14 14 0 0 1 0-4h4.6a14 14 0 0 1 0 4zm.3 5.9c.6-1.2 1-2.5 1.3-3.9h3a8 8 0 0 1-4.3 3.9zM16.3 14a16 16 0 0 0 0-4h3.4a8 8 0 0 1 0 4z"/></svg>www.tomvarulek.net</li>
    </ul>
  </section>

  <section class="card card--front" aria-label="Card front with name">
    <div class="front-block">
      <div class="mark"><span class="mark__ring"></span>Varulek</div>
      <h2 class="front-block__name">Tom Varulek</h2>
      <p class="front-block__role">Front-End Developer</p>
    </div>
  </section>

</body>
</html>
```